Vegan Alfredo Sauce Label Design for Bramble Kitchen Co

We are a food co. committed to making vegan food more accessible to people who want to eat healthier. Our first line of product is vegan Alfredo sauce.
We have 3 flavors:
- Garlic
- Pesto
- Lemony Artichoke
The current project is the design for the first flavor: garlic. However, we would like a template that would translate well to other flavors, so they look like a family of products.
These will be in standard 16 oz jars. The whole label will be approx 6cm x 24cm, but the front visual space is approx 6cm x 10cm. The rest will be nutritional labeling and copy about the company.
We also need a stamp or font- based logo that says Bramble Kitchen Co. (or lower case: bramble kitchen co.), the name of the company.
The picture (attached) of Vegan Queso is the closest to what we are going for. Because the sauce is creamy white, a colorful background with off-white font will be best.
We currently have a website, although we are doing a brand over-haul (hence, this posting) www.bramblekitchenco.example. If the designer is a good fit, we have several more projects, in line.
Other brands we love: Tidy Larder, Marlow Ridge Pantry, Pulp Poured Daily.
The final brand should communicate hip, natural and health.
And personally, I love design that is clever and somehow makes me smile.
Target Market(s)
Vegans, vegetarians, and people with common food allergies - all ages.
Young, hip families.
Industry/Entity Type
It Company
Requirements
Must have
- Copy:
Vegan Alfredo or Vegan Alfredo Sauce
Garlic
Bramble Kitchen or Bramble Kitchen Co
16 oz
Nice to have
- May include copy:
Gluten-Free Soy-Free Nut-Free
Should not have
- Neon colors

```html
<!DOCTYPE html>
<html lang="en">
<head>
<meta charset="utf-8">
<title>Bramble Kitchen Co — Vegan Alfredo Sauce Labels, Option 2</title>
<link rel="stylesheet" href="https://fonts.googleapis.com/css2?family=Cinzel:wght@400&family=Oswald:wght@600&family=Open+Sans:wght@400;600&display=swap">
<style>
  :root {
    --page-bg: #ffffff;
    --ink-heading: #222222;
    --cream: #eef1b4;
    --label-text: #f4f4ea;
    --band-black: #1e1a1d;
    --lemony-gold: #d9c24b;

    --garlic-bg: #8e1f78;
    --garlic-art-a: #6a1a58;
    --garlic-art-b: #571449;

    --artichoke-bg: #4f8a2a;
    --artichoke-art-a: #3f6e25;
    --artichoke-art-b: #365f20;

    --pesto-bg: #7f9d25;
    --pesto-art-a: #6f8a24;
    --pesto-art-b: #627b22;
  }

  * { margin: 0; padding: 0; box-sizing: border-box; }

  html, body {
    width: 1200px;
    height: 900px;
    overflow: hidden;
    background: var(--page-bg);
  }

  .sheet {
    position: relative;
    width: 1200px;
    height: 900px;
  }

  .sheet-title {
    position: absolute;
    left: 25px;
    top: 12px;
    font-family: "Cinzel", serif;
    font-size: 24px;
    letter-spacing: 5px;
    color: var(--ink-heading);
    text-transform: uppercase;
    font-weight: 400;
  }

  .label {
    position: absolute;
    left: 116px;
    width: 968px;
    height: 242px;
    overflow: hidden;
    text-align: center;
  }

  .label--garlic { top: 63px; background: var(--garlic-bg); }
  .label--artichoke { top: 329px; background: var(--artichoke-bg); }
  .label--pesto { top: 594px; background: var(--pesto-bg); }

  .label-art {
    position: absolute;
    inset: 0;
  }

  .label--garlic .label-art {
    background:
      radial-gradient(ellipse 140px 120px at 8% 55%, var(--garlic-art-a), transparent 75%),
      radial-gradient(ellipse 150px 110px at 32% 40%, var(--garlic-art-b), transparent 75%),
      radial-gradient(ellipse 150px 120px at 63% 55%, var(--garlic-art-a), transparent 75%),
      radial-gradient(ellipse 120px 110px at 93% 55%, var(--garlic-art-b), transparent 75%);
    opacity: 0.75;
  }

  .label--artichoke .label-art {
    background:
      radial-gradient(ellipse 110px 130px at 10% 60%, var(--artichoke-art-a), transparent 75%),
      radial-gradient(ellipse 100px 120px at 30% 25%, var(--artichoke-art-b), transparent 75%),
      radial-gradient(ellipse 110px 130px at 67% 40%, var(--artichoke-art-a), transparent 75%),
      radial-gradient(ellipse 100px 120px at 95% 50%, var(--artichoke-art-b), transparent 75%);
    opacity: 0.75;
  }

  .label--pesto .label-art {
    background:
      radial-gradient(ellipse 120px 100px at 14% 55%, var(--pesto-art-a), transparent 75%),
      radial-gradient(ellipse 110px 110px at 36% 20%, var(--pesto-art-b), transparent 75%),
      radial-gradient(ellipse 130px 110px at 72% 45%, var(--pesto-art-a), transparent 75%),
      radial-gradient(ellipse 100px 110px at 93% 65%, var(--pesto-art-b), transparent 75%);
    opacity: 0.75;
  }

  .label-content {
    position: absolute;
    inset: 0;
  }

  .brand-name {
    position: absolute;
    left: 0;
    right: 0;
    top: 23px;
    font-family: "Open Sans", sans-serif;
    font-weight: 600;
    font-size: 15px;
    line-height: 20px;
    color: var(--label-text);
    letter-spacing: -0.2px;
  }

  .flavor-note {
    position: absolute;
    left: 0;
    right: 0;
    top: 51px;
    font-family: "Open Sans", sans-serif;
    font-weight: 600;
    font-size: 15px;
    line-height: 18px;
    letter-spacing: 2.5px;
    color: var(--lemony-gold);
  }

  .flavor-name {
    position: absolute;
    left: 0;
    right: 0;
    font-family: "Oswald", sans-serif;
    font-weight: 600;
    color: var(--cream);
    text-transform: uppercase;
    letter-spacing: 0;
  }

  .label--garlic .flavor-name { top: 45px; font-size: 96px; line-height: 96px; }
  .label--artichoke .flavor-name { top: 69px; font-size: 80px; line-height: 80px; }
  .label--pesto .flavor-name { top: 46px; font-size: 100px; line-height: 100px; }

  .product-band {
    position: absolute;
    left: 363px;
    width: 242px;
    top: 153px;
    height: 22px;
    background: var(--band-black);
    font-family: "Open Sans", sans-serif;
    font-size: 16px;
    line-height: 22px;
    letter-spacing: 1.6px;
    color: var(--label-text);
    white-space: nowrap;
  }

  .free-from {
    position: absolute;
    left: 0;
    right: 0;
    top: 188px;
    font-family: "Open Sans", sans-serif;
    font-size: 9.5px;
    line-height: 14px;
    letter-spacing: 1px;
    color: var(--label-text);
  }

  .net-weight {
    position: absolute;
    left: 0;
    right: 0;
    top: 211px;
    font-family: "Open Sans", sans-serif;
    font-size: 13px;
    line-height: 18px;
    color: var(--label-text);
  }
</style>
</head>
<body>
<main class="sheet">
  <h1 class="sheet-title">Option 2</h1>

  <section class="label label--garlic">
    <div class="label-art" role="img" aria-label="Hand-drawn garlic bulbs illustration in deep purple tones"></div>
    <div class="label-content">
      <p class="brand-name">bramblekitchenco</p>
      <h2 class="flavor-name">Garlic</h2>
      <p class="product-band">VEGAN ALFREDO SAUCE</p>
      <p class="free-from">GLUTEN-FREE • SOY-FREE • NUT-FREE</p>
      <p class="net-weight">16oz</p>
    </div>
  </section>

  <section class="label label--artichoke">
    <div class="label-art" role="img" aria-label="Hand-drawn artichokes illustration in dark green tones"></div>
    <div class="label-content">
      <p class="brand-name">bramblekitchenco</p>
      <p class="flavor-note">LEMONY</p>
      <h2 class="flavor-name">Artichoke</h2>
      <p class="product-band">VEGAN ALFREDO SAUCE</p>
      <p class="free-from">GLUTEN-FREE • SOY-FREE • NUT-FREE</p>
      <p class="net-weight">16oz</p>
    </div>
  </section>

  <section class="label label--pesto">
    <div class="label-art" role="img" aria-label="Hand-drawn basil leaves and garlic illustration in olive green tones"></div>
    <div class="label-content">
      <p class="brand-name">bramblekitchenco</p>
      <h2 class="flavor-name">Pesto</h2>
      <p class="product-band">VEGAN ALFREDO SAUCE</p>
      <p class="free-from">GLUTEN-FREE • SOY-FREE • NUT-FREE</p>
      <p class="net-weight">16oz</p>
    </div>
  </section>
</main>
</body>
</html>
```